MEDICAL CLINIC LETTERHEAD

Design is a letterhead for a non-profit medical center. The name of the clinic is VITARIDGE Community Health Center. Although the full name must be included, the community health center part is more of a description and should be less visible - i attached an example of what I mean by that (ATTACHED IMAGE IS AN EXAMPLE OF FONT SIZES NOT A DESIGN IDEA). Please design something modern, cool looking and unique because I can always download free templates.
Phone, email, website and etc will be added later.

Industry/Entity Type

MEDICAL

```html
<!DOCTYPE html>
<html lang="en">
<head>
<meta charset="utf-8">
<title>VITARIDGE Community Health Center — Letterhead</title>
<link href="https://fonts.googleapis.com/css2?family=Lato:wght@400;700&family=Poppins:wght@300;400&display=swap" rel="stylesheet">
<style>
  :root {
    --backdrop: #e2e3e4;
    --paper: #ffffff;
    --navy: #2f3458;
    --green: #1e8a4c;
    --ink: #1d1d1f;
    --rule: #111111;
    --footer-text: #e9eaf2;
  }
  * { box-sizing: border-box; margin: 0; padding: 0; }
  html, body { width: 1200px; height: 1200px; overflow: hidden; }
  body { background: var(--backdrop); font-family: 'Lato', sans-serif; color: var(--ink); }

  .letterhead {
    position: absolute; left: 190px; top: 20px;
    width: 820px; height: 1160px;
    background: var(--paper);
    box-shadow: 0 4px 18px rgba(0,0,0,0.12);
    overflow: hidden;
  }

  .brand { position: absolute; top: 78px; left: 0; width: 100%; text-align: center; color: var(--navy); }
  .brand-name { font-weight: 700; font-size: 58px; letter-spacing: 4px; line-height: 1; }
  .brand-desc { font-weight: 700; font-size: 13px; letter-spacing: 6px; text-transform: uppercase; margin-top: 10px; }

  .recipient { position: absolute; top: 330px; left: 80px; font-size: 15px; line-height: 19px; }

  .salutation { position: absolute; top: 470px; left: 80px; font-size: 15px; }

  .body-copy { position: absolute; top: 512px; left: 80px; width: 660px; font-size: 14.5px; line-height: 23px; }
  .body-copy span { display: block; white-space: nowrap; }

  .closing { position: absolute; top: 852px; left: 80px; font-size: 15px; }
  .signature { position: absolute; top: 885px; left: 100px; width: 300px; height: 80px; }

  .footer-rule { position: absolute; left: 0; top: 1000px; width: 100%; height: 5px; background: var(--rule); }
  .footer-band {
    position: absolute; left: 0; top: 1012px; width: 100%; height: 148px;
    background: var(--navy); color: var(--footer-text);
    font-family: 'Poppins', sans-serif; text-align: center;
    padding-top: 42px;
  }
  .contact-line { font-size: 15px; font-weight: 400; display: flex; justify-content: center; gap: 22px; align-items: center; }
  .contact-item { display: inline-flex; align-items: center; gap: 6px; }
  .contact-item svg { width: 13px; height: 13px; }
  .contact-item .accent { color: #3fb874; }
  .address-line { font-size: 13.5px; font-weight: 300; margin-top: 14px; }
</style>
</head>
<body>
  <main class="letterhead">
    <header class="brand">
      <div class="brand-name">VITARIDGE</div>
      <div class="brand-desc">Community Health Center</div>
    </header>

    <address class="recipient" style="font-style:normal">
      Mr. Alan Reyes<br>
      President<br>
      Northfield Accountants<br>
      214 Linden Road,<br>
      Riverton State, 54321
    </address>

    <p class="salutation">Dear :</p>

    <p class="body-copy">
      <span>Lorem ipsum dolor sit amet, consectetur adipiscing elit. Aenean ut ipsum eget massa hendrerit</span>
      <span>vestibulum vel in velit. Donec pretium neque velit.</span>
      <span>Aliquam porta lectus nec mauris ornare venenatis. Vivamus non est turpis, et cursus sem. Mauris</span>
      <span>vehicula erat in diam auctor at bibendum nisl lacinia.</span>
      <span>Morbi imperdiet neque vehicula nunc convallis gravida. Vestibulum iaculis pretium placerat. Integer</span>
      <span>consequat, est sit amet facilisis eleifend, nibh nibh varius orci, eget dapibus arcu dui non purus.</span>
      <span>Pellentesque in magna mauris. Duis enim sapien, dictum vitae condimentum a, pulvinar vel lacus.</span>
      <span>Mauris et molestie nibh. Vestibulum vitae nulla at metus elementum porta sit amet interdum elit.</span>
      <span>Nulla sollicitudin neque eu nulla volutpat congue.</span>
      <span>Etiam pellentesque, velit id dapibus fermentum, turpis sapien ornare dui, ac tincidunt ligula odio</span>
      <span>congue purus. Nunc sed ante dui, in porta lectus. Cras nec sem lorem. In hac habitasse platea dictumst.</span>
      <span>Maecenas id diam quis dui porta tristique. Sed id egestas felis. Donec ullamcorper mattis posuere.</span>
      <span>Phasellus fermentum eleifend tortor vel dapibus. Vestibulum ante ipsum.</span>
    </p>

    <p class="closing">Sincerely,</p>
    <svg class="signature" role="img" aria-label="Handwritten signature of Daniel Reyes" viewBox="0 0 300 80">
      <rect width="300" height="80" rx="6" fill="#f1f1f3"/>
    </svg>

    <div class="footer-rule"></div>
    <footer class="footer-band">
      <div class="contact-line">
        <span class="contact-item">
          <svg viewBox="0 0 16 16"><path d="M3 1.5l3 .5 1 3-1.6 1.2a9 9 0 0 0 4.4 4.4L11 9l3 1 .5 3-1.5 1.5C7 14.5 1.5 9 1.5 3z" fill="#3fb874"/></svg>
          0123456789 - 0500000072
        </span>
        <span class="contact-item">
          <svg viewBox="0 0 16 16"><rect x="1.5" y="3.5" width="13" height="9" rx="1" fill="none" stroke="#3fb874" stroke-width="1.6"/><path d="M2 4l6 5 6-5" fill="none" stroke="#3fb874" stroke-width="1.6"/></svg>
          info@vitaridge.com
        </span>
        <span class="contact-item">
          <svg viewBox="0 0 16 16"><circle cx="8" cy="8" r="6.5" fill="none" stroke="#3fb874" stroke-width="1.4"/><ellipse cx="8" cy="8" rx="2.8" ry="6.5" fill="none" stroke="#3fb874" stroke-width="1.2"/><path d="M1.5 8h13" stroke="#3fb874" stroke-width="1.2"/></svg>
          www.<span class="accent">vitaridge</span>.com
        </span>
      </div>
      <div class="address-line">0042 W. Elm Avenue, Suite 120, Harlow, California 90210 &nbsp;|&nbsp; 017 Birch St. Suite 4, Kenton, CA 90118</div>
    </footer>
  </main>
</body>
</html>
```